Personalised nutrition and health DNA report redesign

As part of our DNA report redesign, we are looking for new colour scheme that fits around our brand colours, more professional and slick design and more visual content/less text, but that conveys the same messages. We want it to be more visually appealing to customers and more user friendly and intuitive. We would like to it appeal to both males and females. It would be preferred for it to be done in Adobe InDesign and to receive the source file. I would need all pages redesigned. Thank you!
Target Market(s)
Mostly females, 30-55 but also some younger and middle aged men, professionals interested in their health
Industry/Entity Type
Health tech, Wellness
Look and feel
Each slider illustrates characteristics of the customer's brand and the style your logo design should communicate.

```html
<!DOCTYPE html>
<html lang="en">
<head>
<meta charset="utf-8">
<title>Genevia Nutrition – DNA Report Pages</title>
<link href="https://fonts.googleapis.com/css2?family=Roboto:wght@400;500;700;900&display=swap" rel="stylesheet">
<style>
:root{
  --stage:#5f5f5f;
  --blue:#1f7cf2;
  --blue-mid:#4ea6f2;
  --blue-light:#93cdf6;
  --ink:#111;
  --text:#333;
  --fade:#a9bef7;
  --teal-fade:#a6f0fb;
  --orange:#d9640f;
  --orange-fade:#fbcf9e;
}
*{margin:0;padding:0;box-sizing:border-box}
html,body{width:1200px;height:686px;overflow:hidden;background:var(--stage);font-family:"Roboto",Arial,sans-serif;color:var(--ink)}
.canvas{position:relative;width:1200px;height:686px}
.page{position:absolute;width:206px;height:292px;overflow:hidden;background:linear-gradient(#fff 0%,#fff 66%,var(--fade) 100%)}
.row-top{top:28px}.row-bottom{top:364px}
.col-1{left:30px}.col-2{left:261px}.col-3{left:498px}.col-4{left:730px}.col-5{left:965px}

/* header */
.brand{position:absolute;left:14px;top:12px;font-weight:900;font-size:9.6px;line-height:.92;letter-spacing:-.3px;color:var(--ink)}
.brand span{display:block}
.brand span+span{padding-left:3px}
.tag-band{position:absolute;left:67px;top:14px;width:139px;height:5px;background:var(--blue);color:#fff;font-size:2.7px;letter-spacing:.55px;line-height:5px;text-align:center}

.page-title{position:absolute;left:18px;top:50px;font-size:4.6px;font-weight:700}
.subhead{position:absolute;font-size:3.7px;font-weight:500;color:var(--blue);border-bottom:.4px solid var(--blue);padding-bottom:1px}
.small{font-size:2.5px;line-height:1.35;color:var(--text)}

/* covers */
.cover .art{position:absolute;inset:0}
.cover-brand{position:absolute;left:0;right:0;text-align:center;font-weight:900;color:var(--ink);letter-spacing:-.8px;line-height:.9}
.cover-band{position:absolute;left:0;width:206px;height:5px;background:var(--blue);color:#fff;font-size:3.2px;letter-spacing:.8px;text-align:center;line-height:5px}
.cover-title{position:absolute;left:0;right:0;text-align:center;font-weight:700;font-size:10.8px;letter-spacing:.1px}
.cover-teal{background:linear-gradient(#fff 30%,var(--teal-fade) 100%)}
.cover-orange{background:linear-gradient(#fff 30%,var(--orange-fade) 100%)}
.cover-blue{background:linear-gradient(#fff 30%,var(--fade) 100%)}
.cover-orange .cover-band{background:var(--orange)}

/* letter */
.letter{position:absolute;left:18px;top:50px;width:171px;font-size:2.9px;line-height:1.3;color:var(--text);text-align:justify}
.letter p{margin-bottom:3px}

/* toc */
.toc{position:absolute;left:18px;top:64px;width:108px;list-style:none;font-size:3px;line-height:4.15px;color:var(--text)}
.toc li{display:flex}
.toc li .lead{flex:1;border-bottom:.3px dotted #777;margin:0 2px 1.2px}

/* glossary */
.pill{position:absolute;width:53px;height:9px;border-radius:5px;background:var(--blue);color:#fff;font-size:2.6px;text-align:center;display:flex;align-items:center;justify-content:center;line-height:1.1;padding:0 3px}
.gloss-text{position:absolute;width:46px;font-size:2.2px;line-height:1.35;color:var(--text);text-align:justify}

/* summary */
.bullets{position:absolute;list-style:none;font-size:2.3px;line-height:1.35;color:var(--text)}
.bullets li{margin-bottom:2.6px}
.bullets li::before{content:"• "}
.callout{position:absolute;left:18px;top:200px;width:130px;font-size:3.3px;line-height:1.3;color:var(--blue)}

/* scales */
.scale{position:absolute;height:2px}
.scale.high{background:var(--blue)}
.scale.mid{background:var(--blue-mid)}
.scale.low{background:var(--blue-light)}
.scale i{position:absolute;top:-4px;width:0;height:0;border-left:3px solid transparent;border-right:3px solid transparent;border-top:4px solid currentColor;margin-left:-3px}
.scale.high i{color:var(--blue)}.scale.mid i{color:var(--blue-mid)}.scale.low i{color:var(--blue-light)}
.nutrient{position:absolute;font-size:5.2px;font-weight:500;color:#444;letter-spacing:.1px}
.note{position:absolute;font-size:2.3px;color:var(--text)}
</style>
</head>
<body>
<div class="canvas">

  <!-- Report cover -->
  <section class="page cover cover-blue row-top col-1">
    <svg class="art" viewBox="0 0 206 292" width="206" height="292">
      <path d="M0 0H206V96C170 104 120 110 80 128C45 144 18 160 0 176Z" fill="#0a1430" role="img" aria-label="Glowing blue DNA double helix on a dark background"/>
      <path d="M0 176C18 160 45 144 80 128C120 110 170 104 206 96V110C170 114 126 124 90 140C50 158 20 176 0 194Z" fill="#1f7cf2"/>
      <path d="M206 110V124C172 126 130 136 96 152C60 168 28 185 0 202V194C20 176 50 158 90 140C126 124 170 114 206 110Z" fill="#8b8b8b" opacity=".7"/>
    </svg>
    <div class="cover-brand" style="top:164px;font-size:24px"><div>genevia</div><div>nutrition</div></div>
    <div class="cover-band" style="top:226px">YOUR NUTRITION FOR OPTIMISED HEALTH</div>
    <div class="cover-title" style="top:251px">SAMPLE DNA REPORT</div>
  </section>

  <!-- Welcome letter -->
  <section class="page row-top col-2">
    <div class="brand"><span>genevia</span><span>nutrition</span></div>
    <div class="tag-band">YOUR NUTRITION FOR OPTIMISED HEALTH</div>
    <div class="letter">
      <p>Hi (name)!</p>
      <p>Welcome to your DNA report. Here you will be able to find out about your genetic predispositions to a number of health outcomes like caffeine and salt sensitivity, your sugar and salt preference, optimal times to eat, your body fat response to protein, potential vitamin deficiencies and more! Outcomes we analysed are listed in the <b>table of contents</b> and are organised into different sections (weight management, taste preferences, cardiometabolic health, vitamin and mineral status, and food sensitivities). There is also a summary of your results. But remember, there is much more information and advice for you throughout the report.</p>
      <p>For each outcome, you will be able to see the <b>gene and genetic variant</b> we have tested, <b>your result</b> and explanations on what this means for you. There is also a short <b>glossary</b> of basic terms and links to scientific articles if you would like to know more.</p>
      <p>Please bear in mind that when we talk about nutrigenetics, we are talking about probabilities. While our likelihood of having a specific condition may be increased if we have a specific genetic variant, this does not mean we will 100% have it. Our genes interact with the environment so our diet, lifestyle, exercise regime, all also play an important role.</p>
      <p>In your consultation, I will be explaining your report in detail, and we will agree on key goals that will help you take control of your health.</p>
      <p>I hope you enjoy your report and look forward to embarking with you on this journey to optimised nutrition!</p>
      <p>Dr. Mara Venn</p>
    </div>
  </section>

  <!-- Table of contents -->
  <section class="page row-top col-3">
    <div class="brand"><span>genevia</span><span>nutrition</span></div>
    <div class="tag-band">YOUR NUTRITION FOR OPTIMISED HEALTH</div>
    <h2 class="page-title">TABLE OF CONTENTS:</h2>
    <ul class="toc">
      <li>Glossary of Terms<span class="lead"></span>4</li>
      <li>Summary of Your Results<span class="lead"></span>5</li>
      <li>High Protein Diet<span class="lead"></span>10</li>
      <li>Low Fat Diet<span class="lead"></span>11</li>
      <li>Saturated Fat<span class="lead"></span>12</li>
      <li>Meal Timing<span class="lead"></span>13</li>
      <li>Physical Activity<span class="lead"></span>14</li>
      <li>Cardio Training and Weight<span class="lead"></span>15</li>
      <li>Exercise Motivation<span class="lead"></span>16</li>
      <li>Sugar Preference<span class="lead"></span>18</li>
      <li>Bitter Taster Status<span class="lead"></span>19</li>
      <li>Salt Preference<span class="lead"></span>20</li>
      <li>Salt Sensitivity<span class="lead"></span>22</li>
      <li>Caffeine Sensitivity<span class="lead"></span>23</li>
      <li>Omega-3<span class="lead"></span>24</li>
      <li>Glucose Levels<span class="lead"></span>25</li>
      <li>Glucose and Meal Timing<span class="lead"></span>26</li>
      <li>Insulin Resistance<span class="lead"></span>27</li>
      <li>Vitamin A<span class="lead"></span>29</li>
      <li>Folate And Vitamin B2<span class="lead"></span>30</li>
      <li>Vitamin B12<span class="lead"></span>31</li>
      <li>Vitamin D<span class="lead"></span>32</li>
      <li>Iron Overload<span class="lead"></span>33</li>
      <li>Low Iron Status<span class="lead"></span>34</li>
      <li>Choline<span class="lead"></span>35</li>
      <li>Lactose Tolerance<span class="lead"></span>37</li>
      <li>Gluten Sensitivity<span class="lead"></span>38</li>
    </ul>
  </section>

  <!-- Glossary -->
  <section class="page row-top col-4">
    <div class="brand"><span>genevia</span><span>nutrition</span></div>
    <div class="tag-band">YOUR NUTRITION FOR OPTIMISED HEALTH</div>
    <h2 class="page-title">GLOSSARY OF TERMS</h2>
    <div class="pill" style="left:20px;top:63px">DNA</div>
    <div class="pill" style="left:76px;top:63px">GENE</div>
    <div class="pill" style="left:132px;top:63px">GENETIC VARIANT</div>
    <p class="gloss-text" style="left:24px;top:77px">DNA or deoxyribonucleic acid is a long molecule that contains our unique genetic code. Like a recipe book it holds the instructions for making all the proteins in our bodies. It is built of four letters A, T, C and G, also called nucleotides.</p>
    <p class="gloss-text" style="left:80px;top:77px">A gene is a small section of DNA that contains the instructions for a specific molecule, usually a protein. For example, a gene called FTO holds instructions to create the fat mass and obesity-associated protein, a protein present in the brain and responsible for our response to diet. We all have this gene, but different people have different versions that make their fat mass protein behave or look differently. This is the case for all the genes in our DNA.</p>
    <p class="gloss-text" style="left:136px;top:77px">Every human is unique, but if we were to look at our genes we would find that we are 99.9% the same, genetically speaking. It is the remaining 0.1% that is responsible for all the differences that make each one of us individual. Genetic variants are different versions of the same gene, responsible for these differences.</p>
    <div class="pill" style="left:20px;top:143px">SINGLE NUCLEOTIDE POLYMORPHISM &amp; GENOTYPE</div>
    <div class="pill" style="left:76px;top:143px">NUTRIGENETICS AND NUTRIGENOMICS</div>
    <div class="pill" style="left:132px;top:143px">PERSONALISED NUTRITION</div>
    <p class="gloss-text" style="left:24px;top:157px">The most common form of genetic variants are single nucleotide polymorphisms, describing a change in a single letter in the DNA. They are identified by rs numbers you can see in your report. For the FTO gene, an important genetic variant is a change from letter T to letter A. Since we inherit two copies of the same gene, one from each of our parents, our FTO gene can take one of three forms or versions, TT, TA or AA. These are called Genotypes.</p>
    <p class="gloss-text" style="left:80px;top:157px">Nutrigenetics explores how genetic variants affect the way we respond to different nutrients or types of exercise. Nutrigenomics, on the other hand, explores how the food we eat affects the way our genes are expressed.</p>
    <p class="gloss-text" style="left:136px;top:157px">It uses individual's unique characteristics to tailor nutrition advice and optimise health. These characteristics can be a person's diet, food preferences, body composition, blood markers and DNA, among others.</p>
  </section>

  <!-- Summary: macronutrients -->
  <section class="page row-top col-5">
    <div class="brand"><span>genevia</span><span>nutrition</span></div>
    <div class="tag-band">YOUR NUTRITION FOR OPTIMISED HEALTH</div>
    <h2 class="page-title">SUMMARY OF YOUR RESULTS</h2>
    <div class="subhead" style="left:18px;top:63px;width:80px">MACRONUTRIENT RATIO FOR<br>HEALTHY WEIGHT AND GLUCOSE LEVELS</div>
    <ul class="bullets" style="left:18px;top:78px;width:80px">
      <li>You are a high protein and low carb responder</li>
      <li>For healthy glucose levels, adhere to a dietary pattern such as the Mediterranean diet</li>
    </ul>
    <svg style="position:absolute;left:0;top:0" width="206" height="292" viewBox="0 0 206 292">
      <path d="M149 81L149 45A36 36 0 0 1 178.1 102.2Z" fill="#2e9cf6"/>
      <path d="M149 81L178.1 102.2A36 36 0 0 1 113 81Z" fill="#62b6f8"/>
      <path d="M149 81L113 81A36 36 0 0 1 149 45Z" fill="#1f6ff0"/>
      <g font-family="Roboto, Arial, sans-serif" font-size="2.8" font-weight="700" fill="#fff" text-anchor="middle">
        <text x="137" y="66">Protein</text><text x="137" y="69.5">25%</text>
        <text x="165" y="71">Fat</text><text x="165" y="74.5">35%</text>
        <text x="150" y="96">Carbohydrate</text><text x="150" y="99.5">40%</text>
      </g>
      <g fill="none" stroke="#1f7cf2" stroke-width="1">
        <circle cx="25" cy="111" r="7"/>
        <path d="M25 106.5V111L28 113" stroke-linecap="round"/>
      </g>
      <g fill="#1f7cf2">
        <circle cx="28" cy="155" r="2"/>
        <path d="M21 166L25 158L30 159L33 163L31 164L29 161L27 165L30 168L26 172L25 171L27 168L24 166L22 168Z"/>
      </g>
    </svg>
    <div class="subhead" style="left:18px;top:123px;width:26px">MEAL TIMING</div>
    <ul class="bullets" style="left:18px;top:132px;width:170px">
      <li>Distribute your meals evenly throughout the day</li>
      <li>Avoid high carb meals for breakfast and opt for meals higher in protein for early breakfast and late dinner</li>
    </ul>
    <div class="subhead" style="left:18px;top:170px;width:38px">PHYSICAL ACTIVITY</div>
    <ul class="bullets" style="left:18px;top:179px;width:175px">
      <li>Try and do more than 150 min of moderate/75 min of vigorous intensity per week</li>
      <li>Strength building exercises on 2 days a week (e.g. yoga, pilates, weight training, body weight exercise)</li>
    </ul>
    <p class="callout">FOCUS ON CARDIO TRAINING IF TRYING TO LOSE OR MANAGE WEIGHT, AIM FOR FREQUENT AND SHORTER SESSIONS</p>
  </section>

  <!-- Summary: vitamins -->
  <section class="page row-bottom col-1">
    <div class="brand"><span>genevia</span><span>nutrition</span></div>
    <div class="tag-band">YOUR NUTRITION FOR OPTIMISED HEALTH</div>
    <h2 class="page-title">SUMMARY OF YOUR RESULTS</h2>
    <div class="subhead" style="left:18px;top:63px">VITAMIN AND MINERAL STATUS (LEGEND)</div>
    <div class="scale high" style="left:20px;top:80px;width:85px"><i style="left:3px"></i></div>
    <div class="note" style="left:113px;top:79px">No predisposition for low levels/ typical need</div>
    <div class="scale mid" style="left:20px;top:90px;width:85px"><i style="left:44px"></i></div>
    <div class="note" style="left:113px;top:89px">Medium predisposition for low levels/moderately higher need</div>
    <div class="scale low" style="left:20px;top:100px;width:85px"><i style="left:82px"></i></div>
    <div class="note" style="left:113px;top:99px">High predisposition for low levels/higher need</div>

    <div class="nutrient" style="left:19px;top:124px">VITAMIN A</div>
    <div class="scale high" style="left:20px;top:134px;width:85px"><i style="left:44px"></i></div>
    <div class="nutrient" style="left:114px;top:124px">IRON</div>
    <div class="scale mid" style="left:114px;top:134px;width:79px"><i style="left:76px"></i></div>

    <div class="nutrient" style="left:19px;top:151px">FOLATE AND VITAMIN B2</div>
    <div class="scale mid" style="left:20px;top:161px;width:85px"><i style="left:44px"></i></div>
    <div class="nutrient" style="left:114px;top:151px">CHOLINE</div>
    <div class="scale high" style="left:114px;top:161px;width:79px"><i style="left:76px"></i></div>

    <div class="nutrient" style="left:19px;top:178px">VITAMIN B12</div>
    <div class="scale high" style="left:20px;top:188px;width:85px"><i style="left:44px"></i></div>
    <div class="nutrient" style="left:114px;top:178px">OMEGA-3</div>
    <div class="scale mid" style="left:114px;top:188px;width:79px"><i style="left:40px"></i></div>

    <div class="nutrient" style="left:19px;top:208px">VITAMIN D</div>
    <div class="scale mid" style="left:20px;top:218px;width:85px"><i style="left:44px"></i></div>
  </section>

  <!-- Summary: taste -->
  <section class="page row-bottom col-2">
    <div class="brand"><span>genevia</span><span>nutrition</span></div>
    <div class="tag-band">YOUR NUTRITION FOR OPTIMISED HEALTH</div>
    <h2 class="page-title">SUMMARY OF YOUR RESULTS</h2>
    <div class="subhead" style="left:18px;top:63px">TASTE PREFERENCES</div>
    <ul class="bullets" style="left:18px;top:75px;width:60px;font-size:2.2px">
      <li>You likely have a "sweet tooth"</li>
      <li>You are a medium taster for bitter</li>
      <li>Your preference for salty foods is not high</li>
      <li>Be mindful of your intake of sweet foods</li>
      <li>Follow recommendations for salt intake based on your salt sensitivity genotype.</li>
    </ul>
    <svg style="position:absolute;left:124px;top:40px" width="56" height="90" viewBox="0 0 56 90">
      <defs>
        <linearGradient id="arrowFill" x1="0" y1="0" x2="0" y2="1">
          <stop offset="0" stop-color="#3d63f0"/>
          <stop offset=".6" stop-color="#c9d6fb"/>
          <stop offset="1" stop-color="#fff"/>
        </linearGradient>
      </defs>
      <path d="M28 1L54 25H40V88H16V25H2Z" fill="url(#arrowFill)" stroke="#3d63f0" stroke-width=".6"/>
      <g font-family="Roboto, Arial, sans-serif" font-size="3.2" fill="#222" text-anchor="middle">
        <text x="28" y="28">SWEET</text><text x="28" y="45">BITTER</text><text x="28" y="64">SALTY</text>
      </g>
      <path d="M28 31V40M28 49V59" stroke="#3d63f0" stroke-width=".4"/>
    </svg>

    <div class="nutrient" style="left:18px;top:126px">SALT SENSITIVITY</div>
    <div class="scale high" style="left:18px;top:137px;width:85px"><i style="left:82px"></i></div>
    <div class="note" style="left:106px;top:135px">Blood pressure is sensitive to salt. Eat no more than 4 grams per day</div>

    <div class="nutrient" style="left:18px;top:153px">CAFFEINE SENSITIVITY</div>
    <div class="scale low" style="left:18px;top:164px;width:85px"><i style="left:3px"></i></div>
    <div class="note" style="left:106px;top:160px">You are a fast caffeine metaboliser<br>Your maximal caffeine intake = 400 mg (3-4 cups of coffee daily)</div>

    <div class="nutrient" style="left:18px;top:181px">LACTOSE INTOLERANCE</div>
    <div class="scale low" style="left:18px;top:192px;width:85px"><i style="left:82px"></i></div>
    <div class="note" style="left:106px;top:190px">You may be intolerant to lactose</div>

    <div class="nutrient" style="left:18px;top:208px">GLUTEN SENSITIVITY</div>
    <div class="scale high" style="left:18px;top:219px;width:85px"><i style="left:3px"></i></div>
    <div class="note" style="left:106px;top:217px">You are likely gluten tolerant</div>
  </section>

  <!-- Section cover: weight management -->
  <section class="page cover cover-blue row-bottom col-3">
    <svg class="art" viewBox="0 0 206 292" width="206" height="292">
      <path d="M0 0H206V80C170 90 120 110 70 130C40 142 15 152 0 160Z" fill="#1b7de6" role="img" aria-label="Blue x-ray style human torso skeleton with a DNA helix"/>
      <path d="M0 160C15 152 40 142 70 130C120 110 170 90 206 80V88C168 98 120 120 76 142C44 158 18 172 0 182Z" fill="#050505"/>
      <path d="M206 88V96C170 104 124 124 80 146L76 142C120 120 168 98 206 88Z" fill="#8b8b8b"/>
    </svg>
    <div class="cover-brand" style="top:152px;font-size:24px"><div>genevia</div><div>nutrition</div></div>
    <div class="cover-band" style="top:214px">YOUR NUTRITION FOR OPTIMISED HEALTH</div>
    <div class="cover-title" style="top:250px">WEIGHT MANAGEMENT</div>
  </section>

  <!-- Section cover: taste preferences -->
  <section class="page cover cover-teal row-bottom col-4">
    <svg class="art" viewBox="0 0 206 292" width="206" height="292">
      <path d="M0 0H206V80C170 90 120 110 70 130C40 142 15 152 0 160Z" fill="#19aee0" role="img" aria-label="Teal x-ray style human torso skeleton with a DNA helix"/>
      <path d="M0 160C15 152 40 142 70 130C120 110 170 90 206 80V88C168 98 120 120 76 142C44 158 18 172 0 182Z" fill="#050505"/>
      <path d="M206 88V96C170 104 124 124 80 146L76 142C120 120 168 98 206 88Z" fill="#8b8b8b"/>
    </svg>
    <div class="cover-brand" style="top:152px;font-size:24px"><div>genevia</div><div>nutrition</div></div>
    <div class="cover-band" style="top:214px">YOUR NUTRITION FOR OPTIMISED HEALTH</div>
    <div class="cover-title" style="top:250px">TASTE PREFERENCES</div>
  </section>

  <!-- Section cover: cardiometabolic health -->
  <section class="page cover cover-orange row-bottom col-5">
    <svg class="art" viewBox="0 0 206 292" width="206" height="292">
      <path d="M0 0H206V80C170 90 120 110 70 130C40 142 15 152 0 160Z" fill="#e0650f" role="img" aria-label="Orange x-ray style human torso skeleton with a DNA helix"/>
      <path d="M0 160C15 152 40 142 70 130C120 110 170 90 206 80V88C168 98 120 120 76 142C44 158 18 172 0 182Z" fill="#050505"/>
      <path d="M206 88V96C170 104 124 124 80 146L76 142C120 120 168 98 206 88Z" fill="#8b8b8b"/>
    </svg>
    <div class="cover-brand" style="top:152px;font-size:24px"><div>genevia</div><div>nutrition</div></div>
    <div class="cover-band" style="top:214px">YOUR NUTRITION FOR OPTIMISED HEALTH</div>
    <div class="cover-title" style="top:250px">CARDIOMETABOLIC HEALTH</div>
  </section>

</div>
</body>
</html>
```